20 year old business card needs re-design

We need to redesign our corporate business card look. We need something that appears more modern, eye catchy but professional.

Target Market(s)

manufacturing industry

Industry/Entity Type

Manufacturer

Contact Information for Business Card

One side can have the logo. Other side can have contact information.

Font styles to use
Serif

Colors
3277b5
33b8a4
ffffff

Requirements
Must have
• Eye catchy - need to standout from the crowd. company logo cannot change. Full name, job title, phone number and email address.
Should not have
• Fax, business address is not necessary.

```html
<!DOCTYPE html>
<html lang="en">
<head>
<meta charset="utf-8">
<title>Corvane Industrial Business Card</title>
<link rel="stylesheet" href="https://fonts.googleapis.com/css2?family=Lato:wght@400;700;900&display=swap">
<style>
  :root {
    --stage: #2b2b2d;
    --card-blue: #7f9dd6;
    --card-blue-deep: #5f7fc4;
    --card-white: #ffffff;
    --paper-tint: #eceef0;
    --accent-blue: #3277b5;
    --ink: #1c1c1c;
    --ink-soft: #3a3a3a;
    --rule: #2a2a2a;
  }
  * { box-sizing: border-box; margin: 0; padding: 0; }
  html, body { width: 1200px; height: 1031px; overflow: hidden; }
  body {
    background: var(--stage);
    font-family: "Lato", sans-serif;
    display: flex;
    flex-direction: column;
    align-items: center;
    justify-content: center;
    gap: 48px;
  }
  .card {
    position: relative;
    width: 700px;
    height: 400px;
    border-radius: 22px;
    overflow: hidden;
  }
  .card-pattern {
    position: absolute;
    inset: 0;
    width: 100%;
    height: 100%;
  }
  /* front */
  .card-front { background: var(--card-blue); }
  .card-front .brand {
    position: absolute;
    inset: 0;
    display: flex;
    flex-direction: column;
    align-items: center;
    justify-content: center;
    gap: 6px;
  }
  .brand-name {
    font-weight: 900;
    font-size: 96px;
    letter-spacing: -2px;
    line-height: 1;
    color: var(--ink);
  }
  .brand-sub {
    font-weight: 400;
    font-size: 18px;
    letter-spacing: 14px;
    color: var(--ink);
    border-top: 1.5px solid var(--ink);
    padding-top: 6px;
  }
  /* back */
  .card-back { background: var(--card-white); }
  .card-back .content {
    position: absolute;
    left: 56px;
    top: 46px;
    right: 40px;
  }
  .person-name {
    font-weight: 900;
    font-size: 44px;
    color: var(--accent-blue);
    line-height: 1.05;
    margin-left: 150px;
  }
  .title-row {
    display: flex;
    align-items: flex-end;
    gap: 14px;
    margin-top: 4px;
  }
  .title-rule {
    width: 136px;
    border-bottom: 1.5px solid var(--rule);
    margin-bottom: 8px;
  }
  .person-title {
    font-weight: 400;
    font-size: 33px;
    color: var(--ink);
  }
  .locations {
    margin: 22px 0 0 150px;
    font-size: 17px;
    color: var(--ink);
  }
  .locations .label { color: var(--accent-blue); font-weight: 400; }
  .contact-list {
    list-style: none;
    position: absolute;
    left: 56px;
    bottom: 40px;
    font-size: 18px;
    color: var(--ink-soft);
    display: grid;
    gap: 6px;
  }
  .contact-list li { display: flex; align-items: center; gap: 10px; }
  .contact-list .web { font-weight: 700; color: var(--ink); }
  .contact-icon { width: 16px; height: 16px; flex: none; }
</style>
</head>
<body>
  <section class="card card-front">
    <svg class="card-pattern" role="img" aria-label="Faint white engineering blueprint of gears and mechanical parts over blue" viewBox="0 0 700 400" preserveAspectRatio="none">
      <defs>
        <linearGradient id="frontTone" x1="0" y1="0" x2="1" y2="1">
          <stop offset="0" stop-color="#87a4da"/>
          <stop offset="1" stop-color="#6f8fcf"/>
        </linearGradient>
      </defs>
      <rect width="700" height="400" fill="url(#frontTone)"/>
    </svg>
    <div class="brand">
      <span class="brand-name">Corvane</span>
      <span class="brand-sub">INDUSTRIAL</span>
    </div>
  </section>

  <section class="card card-back">
    <svg class="card-pattern" role="img" aria-label="Very faint grey engineering blueprint of gears and mechanical parts over white" viewBox="0 0 700 400" preserveAspectRatio="none">
      <defs>
        <radialGradient id="backTone" cx="0.5" cy="0.45" r="0.75">
          <stop offset="0" stop-color="#ffffff"/>
          <stop offset="1" stop-color="#e9ebee"/>
        </radialGradient>
      </defs>
      <rect width="700" height="400" fill="url(#backTone)"/>
    </svg>
    <div class="content">
      <h1 class="person-name">Dana Merrow</h1>
      <div class="title-row">
        <span class="title-rule"></span>
        <span class="person-title">Senior Project Manager</span>
      </div>
      <p class="locations"><span class="label">Global Locations:</span> USA, Mexico, China, Taiwan, South Korea, Japan</p>
    </div>
    <ul class="contact-list">
      <li>
        <svg class="contact-icon" viewBox="0 0 16 16"><circle cx="8" cy="8" r="8" fill="var(--accent-blue)"/><path d="M5 4.5c.6-.4 1.2 0 1.5.7l.4.9c.2.4 0 .8-.3 1l-.4.3c.4 1 1.1 1.7 2.1 2.1l.3-.4c.3-.3.7-.5 1-.3l.9.4c.7.3 1.1.9.7 1.5-.5.8-1.4 1-2.3.6C7 10.5 5.5 9 4.7 7 4.3 6 4.4 5 5 4.5z" fill="#fff"/></svg>
        555-014-2270 xt 118
      </li>
      <li>
        <svg class="contact-icon" viewBox="0 0 16 16"><circle cx="8" cy="8" r="8" fill="var(--accent-blue)"/><rect x="4" y="5" width="8" height="6" fill="#fff"/><path d="M4 5l4 3.2L12 5" fill="none" stroke="var(--accent-blue)" stroke-width="1"/></svg>
        dana@corvaneindustrial.com
      </li>
      <li>
        <svg class="contact-icon" viewBox="0 0 16 16"><circle cx="8" cy="8" r="8" fill="var(--accent-blue)"/><circle cx="8" cy="8" r="4.5" fill="none" stroke="#fff" stroke-width="1.2"/><path d="M3.5 8h9M8 3.5c-2 2.5-2 6.5 0 9M8 3.5c2 2.5 2 6.5 0 9" fill="none" stroke="#fff" stroke-width="1"/></svg>
        <span class="web">CorvaneIndustrial.com</span>
      </li>
    </ul>
  </section>
</body>
</html>
```